Upscale business cards needed for Board of Directors

We need professional business cards created for members of our family business Board of Directors. We would like these relatively simple and straightforward, but also with a unique element to set them apart. Probably stick with neutral and simple colors - white, grey etc. We need space for the traditional elements, including name, title, address, email/phone number. And we will be creating several from this template so it needs to be template that is easy to switch information in and out of.
Business
See description

```html
<!DOCTYPE html>
<html lang="en">
<head>
<meta charset="utf-8">
<title>Harborline Holdings — Business Cards</title>
<link href="https://fonts.googleapis.com/css2?family=Lato:wght@400;700;900&display=swap" rel="stylesheet">
<style>
  :root {
    --canvas: #e4e4e2;
    --card-dark: #0b0b0b;
    --card-light: #ffffff;
    --ink: #111111;
    --gold: #b5a27e;
    --white: #ffffff;
  }
  * { box-sizing: border-box; margin: 0; padding: 0; }
  html, body {
    width: 1200px;
    height: 900px;
    overflow: hidden;
    background: var(--canvas);
    font-family: "Lato", sans-serif;
  }
  .canvas {
    position: relative;
    width: 1200px;
    height: 900px;
  }
  .card {
    position: absolute;
    left: 285px;
    width: 630px;
    height: 360px;
    box-shadow: 0 10px 28px rgba(0,0,0,0.18);
  }
  /* Front side */
  .card-front {
    top: 60px;
    background: var(--card-dark);
    color: var(--white);
  }
  .card-front .brand-name {
    position: absolute;
    top: 120px;
    left: 0;
    width: 100%;
    text-align: center;
    font-weight: 900;
    font-size: 44px;
    letter-spacing: 2px;
    line-height: 1.05;
    text-transform: uppercase;
    color: var(--white);
  }
  .card-front .website {
    position: absolute;
    top: 268px;
    left: 0;
    width: 100%;
    text-align: center;
    font-size: 15px;
    letter-spacing: 2px;
    color: var(--white);
  }
  /* Back side */
  .card-back {
    top: 480px;
    background: var(--card-light);
    color: var(--ink);
    border-bottom: 9px solid var(--gold);
  }
  .card-back .brand-name {
    position: absolute;
    top: 100px;
    left: 34px;
    width: 250px;
    text-align: center;
    font-weight: 900;
    font-size: 31px;
    letter-spacing: 1.5px;
    line-height: 1.1;
    text-transform: uppercase;
    color: var(--ink);
  }
  .card-back .divider {
    position: absolute;
    top: 40px;
    left: 318px;
    width: 1.5px;
    height: 270px;
    background: linear-gradient(to bottom, rgba(0,0,0,0), rgba(0,0,0,0.85) 45%, rgba(0,0,0,0));
  }
  .contact {
    position: absolute;
    top: 58px;
    left: 348px;
    width: 260px;
  }
  .contact .person-name {
    font-size: 23px;
    font-weight: 400;
    line-height: 1.1;
  }
  .contact .person-title {
    font-size: 15px;
    color: var(--gold);
    margin-bottom: 12px;
  }
  .contact .address {
    font-size: 16px;
    line-height: 1.25;
    margin-bottom: 8px;
  }
  .contact-list { list-style: none; }
  .contact-list li {
    display: flex;
    align-items: center;
    gap: 12px;
    font-size: 16px;
    line-height: 1.5;
  }
  .contact-list svg {
    width: 14px;
    height: 14px;
    flex: none;
    fill: var(--gold);
  }
</style>
</head>
<body>
<main class="canvas">

  <section class="card card-front" aria-label="Card front">
    <h1 class="brand-name">Harborline<br>Holdings</h1>
    <p class="website">www.harborline.com</p>
  </section>

  <section class="card card-back" aria-label="Card back">
    <h2 class="brand-name">Harborline<br>Holdings</h2>
    <div class="divider"></div>
    <div class="contact">
      <p class="person-name">Daniel Reeves</p>
      <p class="person-title">Director</p>
      <p class="address">1450 Oak Hollow Rd<br>Marlow TX 78100</p>
      <ul class="contact-list">
        <li>
          <svg viewBox="0 0 16 16" aria-hidden="true"><path d="M3.6 1.2l2.3 2.6-1.3 1.9c.9 2 2.7 3.8 4.7 4.7l1.9-1.3 2.6 2.3-1.3 2.3C7.3 15.4.6 8.7.9 2.5z"/></svg>
          <span>512 004 2200</span>
        </li>
        <li>
          <svg viewBox="0 0 16 16" aria-hidden="true"><path d="M4 1h8v4H4zM1 6h14v6h-3v3H4v-3H1zm4 4v4h6v-4z"/></svg>
          <span>512 004 2201</span>
        </li>
        <li>
          <svg viewBox="0 0 16 16" aria-hidden="true"><path d="M1 3h14v1.2L8 9 1 4.2zM1 5.6l7 4.8 7-4.8V13H1z"/></svg>
          <span>info@harborline.com</span>
        </li>
        <li>
          <svg viewBox="0 0 16 16" aria-hidden="true"><path d="M8 1a7 7 0 100 14A7 7 0 008 1zm0 1.3c.8.9 1.4 2.2 1.6 3.9H6.4C6.6 4.5 7.2 3.2 8 2.3zM2.4 7.4h2.8c0 1.3.2 2.5.6 3.6H3.3a5.7 5.7 0 01-.9-3.6zm0-1.2a5.7 5.7 0 014-3.7c-.6 1-1 2.3-1.2 3.7zm4 1.2h3.2c0 1.3-.2 2.5-.6 3.6H7c-.4-1.1-.6-2.3-.6-3.6zm4.4 0h2.8a5.7 5.7 0 01-.9 3.6h-2.5c.4-1.1.6-2.3.6-3.6zm0-1.2c-.2-1.4-.6-2.7-1.2-3.7a5.7 5.7 0 014 3.7zM4.2 12.2h2.3c.4.7.9 1.2 1.5 1.5a5.7 5.7 0 01-3.8-1.5zm5.8 1.5c.6-.3 1.1-.8 1.5-1.5h2.3a5.7 5.7 0 01-3.8 1.5z"/></svg>
          <span>www.harborline.com</span>
        </li>
      </ul>
    </div>
  </section>

</main>
</body>
</html>
```